Business card design for Automotive workshop

We need a business card for a new automotive repair and tyre shop called Keelstone Prime Automotive located in New Zealand. We are a clean, modern and fresh workshop and company.

Front needs to feature logo,
my name:
Marlo Fenwicke (director)

Address:
48 Tarn Lane
Harrowmere 3598

Phone: 07 594 2713
Mobile: 027 451 9362
Email: office@keelstoneautomotive.example.nz
Website: keelstoneautomotive.example.nz

Back needs to feature an area to write down appointment details, date and time.

Also feature a list of jobs and work we do such as,
Vehicle Servicing
All Mechanical Repairs
Warrant of Fitness
Tyres & Wheel Alignments
Automotive Diagnostics
Automotive Parts & Supplies

```html
<!DOCTYPE html>
<html lang="en">
<head>
<meta charset="utf-8">
<title>Keelstone Prime Automotive – Business Card</title>
<link href="https://fonts.googleapis.com/css2?family=Open+Sans:wght@400;700;800&family=Lato:wght@400&display=swap" rel="stylesheet">
<style>
  :root {
    --backdrop: #9bc2cc;
    --card: #1a1a1a;
    --red: #e42228;
    --white: #ffffff;
    --ink: #111111;
  }
  * { margin: 0; padding: 0; box-sizing: border-box; }
  html, body { width: 1200px; height: 965px; overflow: hidden; }
  body {
    background: var(--backdrop);
    font-family: "Open Sans", sans-serif;
    position: relative;
  }
  .card {
    position: absolute;
    left: 275px;
    width: 703px;
    height: 388px;
    background: var(--card);
    border-radius: 22px;
    overflow: hidden;
  }
  .card--front { top: 87px; }
  .card--back { top: 511px; }

  .brand {
    position: absolute;
    color: var(--red);
    font-family: "Open Sans", sans-serif;
    font-weight: 800;
    text-transform: uppercase;
    line-height: 1.05;
  }
  .card--front .brand {
    left: 46px; top: 56px;
    font-size: 22px;
    letter-spacing: 1px;
  }
  .card--back .brand {
    left: 0; right: 0; top: 96px;
    text-align: center;
    font-size: 40px;
    letter-spacing: 2px;
  }

  .contact-list {
    position: absolute;
    left: 24px; top: 220px;
    list-style: none;
  }
  .contact-list li {
    display: flex;
    align-items: center;
    height: 27.5px;
    color: var(--white);
    font-size: 16.5px;
    letter-spacing: 0.2px;
  }
  .contact-list svg { width: 16px; height: 16px; margin-right: 6px; flex: none; }

  .divider {
    position: absolute;
    left: 377px; top: 244px;
    width: 2px; height: 106px;
    background: var(--red);
  }
  .person { position: absolute; left: 397px; top: 236px; }
  .person__name {
    color: var(--red);
    font-weight: 700;
    font-size: 21px;
    letter-spacing: 0.6px;
    line-height: 1.1;
  }
  .person__role {
    color: var(--white);
    font-size: 15px;
    letter-spacing: 0.6px;
    line-height: 1.2;
  }
  .address {
    position: absolute;
    left: 397px; top: 306px;
    color: var(--white);
    font-size: 17px;
    letter-spacing: 0.6px;
  }

  .services {
    position: absolute;
    left: 0; right: 0; top: 265px;
    text-align: center;
    font-family: "Lato", sans-serif;
    font-weight: 400;
    color: var(--red);
    font-size: 16.5px;
    line-height: 27px;
  }
  .appointment {
    position: absolute;
    left: 0; right: 0; bottom: 0;
    height: 42px;
    background: var(--white);
    color: var(--ink);
    font-size: 19px;
    letter-spacing: 0.8px;
  }
  .appointment__field {
    position: absolute;
    top: 8px;
    display: flex;
    align-items: flex-end;
  }
  .appointment__field--time { left: 110px; }
  .appointment__field--date { left: 430px; top: 6px; }
  .appointment__line {
    display: inline-block;
    width: 112px;
    border-bottom: 1.5px solid var(--ink);
    margin-bottom: 5px;
    margin-left: 2px;
  }
</style>
</head>
<body>

<section class="card card--front" aria-label="Business card front">
  <div class="brand">Keelstone Prime<br>Automotive</div>

  <ul class="contact-list">
    <li>
      <svg viewBox="0 0 16 16" aria-hidden="true"><rect x="4" y="1" width="8" height="14" rx="1.5" fill="none" stroke="#e42228" stroke-width="1.6"/><circle cx="8" cy="12.5" r="0.9" fill="#e42228"/></svg>
      + 027 451 9362
    </li>
    <li>
      <svg viewBox="0 0 16 16" aria-hidden="true"><path d="M1 6 C1 3 15 3 15 6 L12 7 L11 5.5 L5 5.5 L4 7 Z" fill="#e42228"/><path d="M4 8 L12 8 L13.5 13 L2.5 13 Z" fill="#e42228"/><circle cx="8" cy="10.5" r="1.3" fill="#1a1a1a"/></svg>
      + 07 594 2713
    </li>
    <li>
      <svg viewBox="0 0 16 16" aria-hidden="true"><rect x="1" y="3.5" width="14" height="9" fill="#e42228"/><path d="M1 3.5 L8 9 L15 3.5" fill="none" stroke="#1a1a1a" stroke-width="1.2"/></svg>
      office@keelstoneautomotive.example.nz
    </li>
    <li>
      <svg viewBox="0 0 16 16" aria-hidden="true"><rect x="1.5" y="2.5" width="13" height="9" fill="none" stroke="#e42228" stroke-width="1.4"/><rect x="6" y="12.5" width="4" height="1.5" fill="#e42228"/><rect x="4" y="14" width="8" height="1" fill="#e42228"/></svg>
      keelstoneautomotive.example.nz
    </li>
  </ul>

  <div class="divider"></div>

  <div class="person">
    <p class="person__name">Marlo Fenwicke</p>
    <p class="person__role">Managing Director</p>
  </div>
  <p class="address">48 Tarn Lane, Harrowmere 3598</p>
</section>

<section class="card card--back" aria-label="Business card back">
  <div class="brand">Keelstone Prime<br>Automotive</div>

  <div class="services">
    <p>Vehicle Servicing / All Mechanical Repairs / Warrant of Fitness</p>
    <p>Tyres &amp; Wheel Alignments / Automotive Diagnostics / Automotive Parts &amp; Supplies</p>
  </div>

  <div class="appointment">
    <div class="appointment__field appointment__field--time">Time<span class="appointment__line"></span></div>
    <div class="appointment__field appointment__field--date">Date<span class="appointment__line"></span></div>
  </div>
</section>

</body>
</html>
```